Brightfen Business Card Redesign & Logo Update

We need to update our business cards to something more modern and fresh. Brightfen can provide the current color schemes and old design examples, but welcome creativity in helping us with this redesign. PLEASE NOTE that we no longer utilize the "tree" and/or "leaf" imagery in our branding. If able would apprecaite an update on the quality of our "words only" logo in Ai. / PNG formats too.

Target Market(s)

Investors, landowners, corporate partners, contractors

Industry/Entity Type

Environmental Restoration & Conservation

Contact Information for Business Card

Logo, persons name, title, mailing address, phone and email, website url

Font styles to use
Other font styles liked:
• Merriweather

Requirements
Nice to have
• Logo, persons name, title, mailing address, phone and email, website url, but open to ideams
Should not have
• No all back backgrounds

```html
<!DOCTYPE html>
<html lang="en">
<head>
<meta charset="utf-8">
<title>Brightfen Business Card</title>
<link rel="stylesheet" href="https://fonts.googleapis.com/css2?family=Oswald:wght@700&family=Open+Sans:wght@400;700&display=swap">
<style>
  :root {
    --stage: #dcdcdc;
    --card-top: #3a3f44;
    --card-bottom: #2b2f33;
    --edge: #f07f1e;
    --orange: #f07f1e;
    --green: #2a9a52;
    --ink: #f2f2f2;
    --soft: #dcdcdc;
    --silver: #c4c4c4;
  }
  * { margin: 0; padding: 0; box-sizing: border-box; }
  html, body { width: 1200px; height: 801px; overflow: hidden; }
  body {
    background: var(--stage);
    font-family: "Open Sans", Arial, sans-serif;
    position: relative;
  }
  .card {
    position: absolute;
    top: 246px;
    width: 540px;
    height: 309px;
    background: linear-gradient(160deg, var(--card-top) 0%, var(--card-bottom) 100%);
    border: 1.5px solid var(--edge);
    border-radius: 16px;
    box-shadow: 0 14px 30px rgba(0,0,0,.25);
  }
  .card--front { left: 40px; }
  .card--back { left: 620px; }

  .wordmark {
    font-family: "Oswald", Impact, sans-serif;
    font-weight: 700;
    text-transform: uppercase;
    line-height: 1;
    white-space: nowrap;
  }
  .card--front .wordmark {
    position: absolute;
    top: 34px;
    right: 38px;
    font-size: 44px;
    color: var(--orange);
    letter-spacing: 1px;
  }
  .card--back .wordmark {
    position: absolute;
    top: 50%;
    left: 50%;
    transform: translate(-50%, -50%);
    font-size: 72px;
    color: var(--silver);
    letter-spacing: 2px;
  }

  .person {
    position: absolute;
    left: 38px;
    top: 138px;
  }
  .person__name {
    font-weight: 700;
    font-size: 19px;
    line-height: 24px;
    color: var(--orange);
    text-transform: uppercase;
    letter-spacing: .5px;
  }
  .person__title {
    font-size: 15px;
    line-height: 20px;
    color: var(--ink);
    margin-top: 2px;
  }
  .divider {
    position: absolute;
    left: 38px;
    right: 38px;
    top: 196px;
    height: 1px;
    background: var(--orange);
  }
  .contacts {
    position: absolute;
    left: 38px;
    top: 208px;
    list-style: none;
  }
  .contacts li {
    display: flex;
    align-items: center;
    gap: 8px;
    font-size: 14px;
    color: var(--ink);
    line-height: 25px;
    white-space: nowrap;
  }
  .contacts svg { width: 12px; height: 12px; fill: var(--green); flex: none; }
  .address {
    position: absolute;
    right: 38px;
    top: 212px;
    text-align: right;
    font-size: 14px;
    line-height: 24px;
    color: var(--soft);
    font-style: normal;
    white-space: nowrap;
  }
</style>
</head>
<body>
  <section class="card card--front" aria-label="Business card front">
    <div class="wordmark">Brightfen</div>

    <div class="person">
      <div class="person__name">Erin Caldwell</div>
      <div class="person__title">President</div>
    </div>

    <div class="divider"></div>

    <ul class="contacts">
      <li>
        <svg viewBox="0 0 24 24" aria-hidden="true"><path d="M6.6 10.8a15.1 15.1 0 0 0 6.6 6.6l2.2-2.2a1 1 0 0 1 1-.25 11.4 11.4 0 0 0 3.6.57 1 1 0 0 1 1 1V20a1 1 0 0 1-1 1A17 17 0 0 1 3 4a1 1 0 0 1 1-1h3.5a1 1 0 0 1 1 1c0 1.25.2 2.45.57 3.57a1 1 0 0 1-.25 1z"/></svg>
        555-014-2290
      </li>
      <li>
        <svg viewBox="0 0 24 24" aria-hidden="true"><path d="M2 5h20v14H2z M2 5l10 8 10-8"/></svg>
        ecaldwell@brightfen.com
      </li>
      <li>
        <svg viewBox="0 0 24 24" aria-hidden="true"><circle cx="12" cy="12" r="10"/></svg>
        www.brightfen.com
      </li>
    </ul>

    <address class="address">
      1180 Harbor View Dr<br>
      Cove Bay CA 90210
    </address>
  </section>

  <section class="card card--back" aria-label="Business card back">
    <div class="wordmark">Brightfen</div>
  </section>
</body>
</html>
```